Coastline Premier Retreats Business Card Design

Design a business card for Coastline Premier Retreats. Look at the website for colors and reference. Card should have logo, name, title, office number, mobile number, email, URL and a tagline like, "Luxury Hotel & Resort Email Marketing" (This might change).

https://www.coastlinepremierretreats.example

The rest I will leave up to your imagination.

Contact Information for Business Card

Logo, name, title, office number, mobile number, email, URL and a tagline like, "Luxury Hotel & Resort Email Marketing" (This might change).

```html
<!DOCTYPE html>
<html lang="en">
<head>
<meta charset="utf-8">
<title>Coastline Premier Retreats – Business Card</title>
<link rel="stylesheet" href="https://fonts.googleapis.com/css2?family=Roboto:wght@400;700;900&display=swap">
<style>
  :root {
    --stage: #1c1c1e;
    --card-white: #ffffff;
    --brand-orange: #f37421;
    --ink: #111111;
    --photo-top: #4f7fb0;
    --photo-bottom: #1d8f92;
  }
  * { box-sizing: border-box; margin: 0; padding: 0; }
  html, body {
    width: 1200px; height: 900px; overflow: hidden;
    background: var(--stage);
    font-family: "Roboto", Arial, sans-serif;
  }
  .canvas {
    width: 1200px; height: 900px;
    display: flex; flex-direction: column; align-items: center; justify-content: center;
    gap: 40px;
  }
  .card {
    position: relative;
    width: 640px; height: 366px;
    border-radius: 26px;
    overflow: hidden;
    box-shadow: 0 14px 30px rgba(0,0,0,.45);
  }
  /* Front */
  .card-front { background: var(--card-white); color: var(--ink); }
  .card-front .swoosh { position: absolute; inset: 0; width: 100%; height: 100%; }
  .brand-name {
    position: absolute; left: 40px; top: 72px;
    font-weight: 900; font-size: 25px; line-height: 1.1;
    color: var(--ink); letter-spacing: .5px; text-transform: uppercase;
    width: 280px;
  }
  .divider {
    position: absolute; left: 348px; top: 92px;
    width: 2px; height: 180px; background: var(--brand-orange);
  }
  .contact-block { position: absolute; left: 366px; top: 90px; width: 262px; }
  .person-name {
    color: var(--brand-orange); font-weight: 700; font-size: 21px;
    text-transform: uppercase; letter-spacing: .4px; margin-bottom: 4px;
  }
  .person-role, .tagline { font-size: 15px; line-height: 1.3; }
  .tagline { margin-bottom: 10px; }
  .contact-list { list-style: none; }
  .contact-list li {
    display: flex; align-items: center; gap: 7px;
    font-size: 12.5px; line-height: 1.6; white-space: nowrap;
  }
  .contact-list svg { width: 13px; height: 13px; flex: none; fill: var(--brand-orange); }
  /* Back */
  .card-back .photo-area {
    position: absolute; inset: 0;
    background: linear-gradient(180deg, var(--photo-top) 0%, var(--photo-bottom) 100%);
  }
  .card-back .brand-name-large {
    position: absolute; inset: 0;
    display: flex; align-items: center; justify-content: center; text-align: center;
    color: var(--card-white); font-weight: 900; font-size: 40px;
    letter-spacing: 1px; text-transform: uppercase; line-height: 1.1;
    padding: 0 60px;
  }
</style>
</head>
<body>
<main class="canvas">
  <section class="card card-front" aria-label="Business card front">
    <svg class="swoosh" viewBox="0 0 640 366" preserveAspectRatio="none" aria-hidden="true">
      <path d="M0,185 C140,225 300,290 400,330 C450,350 490,362 520,366 L0,366 Z" fill="var(--brand-orange)"/>
      <path d="M0,150 C150,185 330,270 470,345 C340,290 160,215 0,170 Z" fill="var(--ink)"/>
    </svg>

    <div class="brand-name">Coastline Premier Retreats</div>

    <div class="divider"></div>

    <div class="contact-block">
      <p class="person-name">Daniel Marlowe</p>
      <p class="person-role">Co-Founder</p>
      <p class="tagline">Luxury Hotel &amp; Resort<br>Email Marketing</p>
      <ul class="contact-list">
        <li>
          <svg viewBox="0 0 24 24"><path d="M6.6 10.8a15 15 0 0 0 6.6 6.6l2.2-2.2a1 1 0 0 1 1-.25 11.4 11.4 0 0 0 3.6.6 1 1 0 0 1 1 1V20a1 1 0 0 1-1 1A17 17 0 0 1 3 4a1 1 0 0 1 1-1h3.5a1 1 0 0 1 1 1c0 1.25.2 2.45.6 3.6a1 1 0 0 1-.25 1z"/></svg>
          555-201-4836
        </li>
        <li>
          <svg viewBox="0 0 24 24"><path d="M7 1h10a2 2 0 0 1 2 2v18a2 2 0 0 1-2 2H7a2 2 0 0 1-2-2V3a2 2 0 0 1 2-2zm0 3v14h10V4zm5 15.5a1.2 1.2 0 1 0 0 2.4 1.2 1.2 0 0 0 0-2.4z"/></svg>
          555-307-6192
        </li>
        <li>
          <svg viewBox="0 0 24 24"><path d="M2 5h20v14H2zm2 2v.5l8 5 8-5V7zm0 2.9V17h16V9.9l-8 5z"/></svg>
          info@coastlinepremierretreats.example
        </li>
        <li>
          <svg viewBox="0 0 24 24"><path d="M12 2a10 10 0 1 0 0 20 10 10 0 0 0 0-20zm0 2a8 8 0 0 1 7.7 6H4.3A8 8 0 0 1 12 4zm-7.7 8h15.4A8 8 0 0 1 12 20a8 8 0 0 1-7.7-8z"/></svg>
          www.coastlinepremierretreats.example
        </li>
      </ul>
    </div>
  </section>

  <section class="card card-back" aria-label="Business card back">
    <div class="photo-area" role="img" aria-label="Photograph of a rocky coastline with pine trees and turquoise sea"></div>
    <div class="brand-name-large">Coastline Premier Retreats</div>
  </section>
</main>
</body>
</html>
```